July 2022 Industrial Manufacturer Product Expo Mexico City

We manufacture large screws and fastners for large Mining equipment, Trains, large ships, airplanes, wind turbines, and so on. We also do custom work base on the customer needs. No matter the size we can make it.
We have a Expo coming up with companies all over the world. We have to stand out we are a family own business so our customer service will be above and beyond anyone can provide. We do not have a sales force to push our products and services we provide one on one service.
Plus@!! I'm looking for anything that you designers can come up with if it was your company to put on a business card, plus i want to do a 1 or 2 sided pamphlet, and then a website. We make Speciality Bolts for large mining equipment these bolts can be 3 to 4 foot long!!! Plus fasteners, Nuts, washers, any, size, strengths, special materials, we offer more of a ono on one customer service, We are a small company, family own, but can fulfill any type of orders. We can also provide special time lines for emergency orders. "We keep the machines running we here at KRV don't believe in down time" We want to hear any slogan based on our company to stand out.
Thanks i really appreciate all your work and options that we have to pick on. Plus just a thought we could possibly want to entertain a experience Marketing internet help maybe a employment possibility. Thanks

I need 2 cards one in Spanish and English Like the steel back ground maybe send me in some bright red and blue writing Same with the Black cards Please remove the word Military The logo KRV maybe integrate a picture of a Bolt 🔩 Thank you

Still looking for I need 2 cards one in Spanish and English Like the steel back ground maybe send me in some bright red and blue writing Same with the Black cards try bright writing Please remove the word Military The logo KRV maybe integrate a picture of a Bolt 🔩 Plus will need the company to make a brochure and website next Thank you

Target Market(s)

Large Mining, Ship, Train, Green Energy, VELM, and Government equipment. Throughout the World

Industry/Entity Type

We can Custom Manufacture any type of Fastners for Mining equipment, Trains, Ships, Green energy, Governments, or military projects. wind turbines,

Contact Information for Business Card

I attached the name and contact info that's on a card, plus the Company Logo. Would like industrial looking background with Bright Colors that will stand out!! If we can insert somewhere maybe on back that we "Custom Manufacture Any Size or Quantity Fastners for Large Mining Equipment, Trains, Ships, Green Energy Equipment or Government Projects

Font styles to use
Other font styles liked:
• You Pick, has to be bold, colorful standout, Professional looking Beable to read it.

Colors

Designer to choose colors to be used in the design.

Requirements
Must have
• Need in Spanish and English TO STANDOUT FROM THE REST OF THE EXPO!! See Business card details, Rounded corners
Nice to have
• Can i see some of the darker cards with Bright Red and Blue letters I like to see the different type of card material, heavy thickness, plastic, transparent, Metal types, Bright Colors, I saw like Raised letters like on the logo.

```html
<!DOCTYPE html>
<html lang="es">
<head>
<meta charset="utf-8">
<title>KRV Business Cards</title>
<link rel="stylesheet" href="https://fonts.googleapis.com/css2?family=Cinzel:wght@400;600&family=Open+Sans:wght@400;600;700&display=swap">
<style>
  :root {
    --page-bg: #2a2a2a;
    --card-black: #141414;
    --card-white: #ffffff;
    --edge-navy: #0d1f8a;
    --bright-blue: #1a8fd6;
    --navy-text: #16237a;
    --logo-grey: #4a4a4e;
  }
  * { margin: 0; padding: 0; box-sizing: border-box; }
  html, body {
    width: 1200px; height: 1015px; overflow: hidden;
    background: var(--page-bg);
  }
  .stage {
    position: relative; width: 1200px; height: 1015px;
  }
  .card {
    position: absolute; left: 250px; width: 700px; height: 400px;
    border-radius: 6px; overflow: hidden;
    border-bottom: 7px solid var(--edge-navy);
    box-shadow: 0 10px 26px rgba(0,0,0,0.5);
  }
  /* Back side */
  .card--back {
    top: 82px; background: var(--card-black);
    display: flex; align-items: center; justify-content: center;
  }
  .services {
    font-family: "Cinzel", serif; font-weight: 600;
    color: var(--bright-blue); font-size: 21px; line-height: 1.45;
    letter-spacing: 0.5px; text-align: left;
  }
  .services span { display: block; }
  .services span:nth-child(2) { padding-left: 30px; }
  .services span:nth-child(3) { padding-left: 44px; }
  .services span:nth-child(4) { padding-left: 78px; }
  /* Front side */
  .card--front { top: 532px; background: var(--card-white); }
  .brand {
    position: absolute; top: 58px; right: 70px;
    font-family: "Open Sans", sans-serif; font-weight: 700;
    font-size: 96px; letter-spacing: 18px; line-height: 1;
    color: var(--logo-grey);
  }
  .name {
    position: absolute; left: 58px; top: 232px;
    font-family: "Open Sans", sans-serif; font-weight: 700;
    font-size: 30px; color: var(--bright-blue);
  }
  .divider {
    position: absolute; left: 58px; right: 52px; top: 284px;
    height: 1.5px; background: var(--navy-text);
  }
  .phones {
    position: absolute; right: 52px; top: 218px;
    font-family: "Open Sans", sans-serif; font-size: 19px;
    color: var(--navy-text); line-height: 1.35; text-align: right;
  }
  .phone { display: flex; align-items: center; justify-content: flex-end; gap: 6px; }
  .phone svg { width: 18px; height: 18px; }
  .quotes {
    position: absolute; left: 58px; top: 306px;
    font-family: "Open Sans", sans-serif; font-size: 22px;
    color: var(--navy-text); line-height: 1.3;
  }
</style>
</head>
<body>
<main class="stage">
  <section class="card card--back" aria-label="Reverso de la tarjeta">
    <p class="services">
      <span>Custom Manufacture Any Size or Quantity</span>
      <span>Fastners for Large Mining Equipment</span>
      <span>Trains, Ships, Green Energy Equipment</span>
      <span>Military or Government Projects</span>
    </p>
  </section>

  <section class="card card--front" aria-label="Frente de la tarjeta">
    <div class="brand">KRV</div>
    <h1 class="name">Lic.Mariela Sofía Ortega Ruiz</h1>
    <div class="phones">
      <div class="phone">5550193601
        <svg viewBox="0 0 24 24" aria-hidden="true"><path fill="#1a8fd6" d="M6.6 10.8a15 15 0 0 0 6.6 6.6l2.2-2.2a1 1 0 0 1 1-.25 11.4 11.4 0 0 0 3.6.6 1 1 0 0 1 1 1V20a1 1 0 0 1-1 1A17 17 0 0 1 3 4a1 1 0 0 1 1-1h3.5a1 1 0 0 1 1 1c0 1.25.2 2.45.57 3.57a1 1 0 0 1-.25 1z"/></svg>
      </div>
      <div class="phone">5550127600
        <svg viewBox="0 0 24 24" aria-hidden="true"><rect x="6" y="2" width="12" height="20" rx="2" fill="none" stroke="#1a8fd6" stroke-width="2"/><circle cx="12" cy="18" r="1.2" fill="#1a8fd6"/></svg>
      </div>
    </div>
    <div class="divider"></div>
    <p class="quotes">Cotizaciones en<br>tornilleriakrv.ventas@example.com</p>
  </section>
</main>
</body>
</html>
```